Banner ads for LP that work with same theme as below banners

Love the banner ads below. Need more with attached photos. But use the same wording, font as in below banner ads. Should be LP size 1200/627 so I can use for Pixorly and LP. Looking for great ads to use as LP ads. We do lots of ads so it will be worth your time to enter this contest you will be rewarded with a ton of work. Need several banner ads that work together. So maybe 1 of the dresses, 1 of the sweater, 1 of the leggings, 1 of the jacket

Target Market(s)

Women 24-45

Industry/Entity Type

Fashion

Requirements
Must have
• Banner ads that work for LP and Pixorly
Nice to have
• Several options to choose from
Should not have
• not sure

```html
<!DOCTYPE html>
<html lang="en">
<head>
<meta charset="utf-8">
<title>Our Best Dresses Ever – Banner</title>
<link href="https://fonts.googleapis.com/css2?family=Dancing+Script:wght@600&family=Playfair+Display:wght@700&family=Libre+Baskerville:wght@700&display=swap" rel="stylesheet">
<style>
  :root {
    --paper: #ffffff;
    --bronze: #7b5a2c;
    --stone: #cac7c3;
    --stone-light: #d6d4d1;
    --stone-dark: #bdb9b4;
    --frame: #d9d9d9;
    --ink: #111111;
    --ink-soft: #4a4a4a;
    --button-top: #6a6a6a;
    --button-bottom: #2e2e2e;
    --button-text: #f2f2f2;
  }
  html, body {
    margin: 0;
    padding: 0;
    overflow: hidden;
    background: var(--paper);
  }
  .banner {
    position: relative;
    width: 1200px;
    height: 627px;
    overflow: hidden;
    background: var(--paper);
  }
  .band-top {
    position: absolute;
    left: 0; top: 0;
    width: 640px; height: 76px;
    background: var(--bronze);
    clip-path: polygon(0 0, 100% 0, 89% 100%, 0 100%);
  }
  .band-left {
    position: absolute;
    left: 0; top: 76px;
    width: 220px; height: 430px;
    background: var(--stone-dark);
  }
  .band-right {
    position: absolute;
    left: 1020px; top: 26px;
    width: 180px; height: 494px;
    background: var(--stone-light);
  }
  .band-bottom {
    position: absolute;
    left: 800px; top: 574px;
    width: 400px; height: 53px;
    background: var(--bronze);
    clip-path: polygon(3% 0, 100% 0, 100% 100%, 0 100%);
  }
  .panel {
    position: absolute;
    left: 204px; top: 32px;
    width: 826px; height: 492px;
    background: var(--stone);
    box-shadow: 0 6px 18px rgba(0,0,0,0.25);
  }
  .photo-frame {
    position: absolute;
    background: var(--paper);
    border: 7px solid var(--frame);
    box-shadow: 0 8px 22px rgba(0,0,0,0.28);
    box-sizing: border-box;
  }
  .photo-frame--hero {
    left: 117px; top: 111px;
    width: 504px; height: 504px;
    transform: rotate(-22deg);
  }
  .photo-frame--inset {
    left: 760px; top: 345px;
    width: 240px; height: 240px;
    transform: rotate(-14deg);
  }
  .photo {
    position: absolute;
    inset: 0;
  }
  .photo--dress {
    background:
      radial-gradient(ellipse 30% 25% at 55% 28%, #c98d5a 0%, rgba(201,141,90,0) 100%),
      radial-gradient(ellipse 45% 55% at 55% 70%, #3b2a2a 0%, #2a4f7a 55%, rgba(255,255,255,0) 100%),
      #f6f3f0;
  }
  .photo--sweater {
    background:
      radial-gradient(ellipse 40% 30% at 55% 30%, #6b4a3a 0%, rgba(107,74,58,0) 100%),
      radial-gradient(ellipse 45% 45% at 55% 85%, #1f2438 0%, rgba(31,36,56,0) 100%),
      #f7f7f7;
  }
  .headline {
    position: absolute;
    left: 630px; top: 38px;
    width: 400px;
    margin: 0;
    text-align: center;
    font-weight: normal;
  }
  .headline__script {
    display: block;
    font-family: "Dancing Script", cursive;
    font-weight: 600;
    font-size: 66px;
    line-height: 1;
    color: var(--ink);
  }
  .headline__script--lead { margin-left: -20px; }
  .headline__script--tail { margin-left: -40px; margin-top: -6px; }
  .headline__caps {
    display: block;
    font-family: "Playfair Display", serif;
    font-weight: 700;
    font-size: 66px;
    letter-spacing: 14px;
    line-height: 1.25;
    color: var(--ink-soft);
    margin-right: -14px;
  }
  .cta {
    position: absolute;
    left: 724px; top: 518px;
    width: 344px; height: 80px;
  }
  .cta svg {
    position: absolute;
    inset: 0;
  }
  .cta__label {
    position: absolute;
    inset: 0;
    display: flex;
    align-items: center;
    justify-content: center;
    gap: 10px;
    font-family: "Libre Baskerville", serif;
    font-weight: 700;
    color: var(--button-text);
    text-decoration: none;
    letter-spacing: 0.5px;
    transform: rotate(-2deg);
  }
  .cta__word--big { font-size: 32px; }
  .cta__word { font-size: 28px; }
</style>
</head>
<body>
  <main class="banner">
    <div class="band-top"></div>
    <div class="band-left"></div>
    <div class="band-right"></div>
    <div class="panel"></div>
    <div class="band-bottom"></div>

    <figure class="photo-frame photo-frame--hero" style="margin:0">
      <div class="photo photo--dress" role="img" aria-label="Model in a black lace dress with blue floral print"></div>
    </figure>

    <figure class="photo-frame photo-frame--inset" style="margin:0">
      <div class="photo photo--sweater" role="img" aria-label="Model in a navy top with red embroidered neckline"></div>
    </figure>

    <h1 class="headline">
      <span class="headline__script headline__script--lead">Our Best</span>
      <span class="headline__caps">DRESSES</span>
      <span class="headline__script headline__script--tail">Ever!</span>
    </h1>

    <a class="cta" href="#">
      <svg width="344" height="80" viewBox="0 0 344 80" aria-hidden="true">
        <defs>
          <linearGradient id="ctaFill" x1="0" y1="0" x2="0" y2="1">
            <stop offset="0" stop-color="var(--button-top)"/>
            <stop offset="1" stop-color="var(--button-bottom)"/>
          </linearGradient>
        </defs>
        <polygon points="4,10 340,2 334,70 0,78" fill="url(#ctaFill)"/>
        <polygon points="4,10 340,2 338,10 6,17" fill="rgba(255,255,255,0.18)"/>
      </svg>
      <span class="cta__label">
        <span class="cta__word--big">SHOP</span>
        <span class="cta__word">THE LOOK</span>
      </span>
    </a>
  </main>
</body>
</html>
```